Valdo Capital

We need a corporate style website design for a new company based in Shenzhen's Qianhai Special Economic Development Zone, China. We provide a range of financial services to large international investment companies. Typically these companies invest over 5 million RMB. The company is part of a group that consists of NorthKilns, ValdoTrusts and ValdoEquity. Our location and gateway into Qianhai Special Economic Zone is our core advantage. We would like to see designs that Do Not use purple and orange. The website design should be similar to other websites in this family but different enough to give it a unique style (See attached website links for reference). The final design should communicate financial safety and growth. This website will act partly as a business chamber with connections to the government so we would like it to be diplomatic in style.

www.northkilns.example
www.valdotrusts.example

*Nevegation Bar
Should including Homepage, Financial Product, Team, News.
Could refer to www.valdotrusts.example

*Contact Details

Miss Lan
Address:E 728, North Block, KMO Centre, East Sector, Shenzhen Bright Science Campus
Telephone: +86 0755 63920417
Cellphone: +86 13957280316

* Social Media
Should be grouped like:
1. Weibo QRcode+ Weibo
2. Facebook, Twitter, Linkedin.

Industry/Entity Type

Investment

```html
<!DOCTYPE html>
<html lang="en">
<head>
<meta charset="utf-8">
<title>Valdo Capital</title>
<link href="https://fonts.googleapis.com/css2?family=Open+Sans:ital,wght@0,400;0,600;0,700;1,400&display=swap" rel="stylesheet">
<style>
:root{
  --ink:#3a3a3a;--text:#555;--muted:#8a8a8a;--blue:#1e9ad6;--page:#eeeeee;
  --white:#fff;--topbar:#393939;--footer:#3d3d3d;--footer-bottom:#303030;--hex:#3b3b3b;
}
*{box-sizing:border-box;margin:0;padding:0}
html,body{width:862px;height:1200px;overflow:hidden}
body{position:relative;background:var(--page);font-family:"Open Sans",Arial,sans-serif;color:var(--text)}
.abs{position:absolute}
.topbar{left:0;top:0;width:862px;height:24px;background:var(--topbar);color:#ddd;font-size:9px;display:flex;justify-content:flex-end;align-items:center;gap:14px;padding-right:87px}
.topbar span{display:flex;align-items:center;gap:5px}
.brand{left:86px;top:30px;display:flex;align-items:center;gap:8px;font-size:19px;font-weight:600;color:var(--ink);height:50px}
.brand-mark{width:12px;height:12px;background:var(--blue)}
.nav{left:393px;top:24px;height:64px;display:flex;font-size:9.5px;color:var(--ink)}
.nav a{display:flex;align-items:center;padding:0 12px;color:inherit;text-decoration:none}
.nav a.active{background:var(--white);padding:0 16px;border-bottom:2px solid var(--blue);position:relative}
.nav a.active::after{content:"";position:absolute;left:50%;bottom:-5px;width:6px;height:6px;margin-left:-3px;background:var(--blue);transform:rotate(45deg)}
.rule{left:86px;top:87px;width:690px;height:1px;background:#cfcfcf}
.hero{left:86px;top:108px;width:690px;height:290px;border-top:3px solid var(--blue);background:linear-gradient(180deg,#3c4f78 0%,#5a6f98 35%,#2c3c5c 62%,#8a6a3a 85%,#2e3550 100%)}
.hero-caption{left:134px;top:214px;width:245px;height:106px;background:rgba(20,20,25,.82);color:#eee;padding:6px 10px}
.hero-caption h1{font-size:21px;font-weight:600;color:#fff;margin-bottom:3px}
.hero-caption p{font-size:9px;line-height:14px}
.hero-caption .more{font-size:9.5px;margin-top:5px;color:#fff}
.arrow{top:232px;width:35px;height:35px;background:rgba(25,25,25,.85);display:flex;align-items:center;justify-content:center}
.service{top:443px;width:197px;height:92px;background:var(--white);text-align:center;padding-top:18px}
.service h3{font-size:9.5px;font-weight:600;color:var(--ink);margin-bottom:8px}
.service p{font-size:8px;line-height:12px;color:var(--muted);padding:0 14px}
.hex{top:421px;width:40px;height:44px}
.section-title{font-size:13.5px;color:var(--ink)}
.tile{top:588px;width:159px;height:140px;background:var(--white)}
.tile .img{height:111px}
.tile .cap{height:29px;display:flex;align-items:center;justify-content:center;font-size:11px;color:var(--ink)}
.tile.active{border-bottom:2px solid var(--blue)}
.welcome h2,.quote h2{font-size:16px;font-weight:400;color:var(--ink)}
.welcome h2 em{font-style:normal;color:var(--blue)}
.welcome p{font-size:8.7px;line-height:12.2px;color:var(--text);width:460px}
.welcome p.first{margin-top:13px}
.welcome p.second{margin-top:12px}
.btn{height:19px;background:var(--blue);color:#fff;font-size:8.5px;font-weight:700;border-radius:2px;display:flex;align-items:center;justify-content:center}
.field{left:592px;width:174px;background:var(--white);border:1px solid #d6d6d6;font-size:7.5px;font-style:italic;color:#666;padding:4px 7px}
.footer{left:0;top:957px;width:862px;height:208px;background:var(--footer);color:#aaa;font-size:8.2px;line-height:13.5px}
.footer h4{font-size:9.5px;font-weight:400;color:#eee;margin-bottom:16px}
.foot-col{top:35px}
.social{display:flex;gap:4px;margin-top:14px}
.social i{width:29px;height:29px;background:#353535;display:block}
.social i.on{background:#6a6a6a}
.bottom{left:0;top:1165px;width:862px;height:35px;background:var(--footer-bottom);font-size:8px;color:#777;display:flex;align-items:center;justify-content:space-between;padding:0 84px 0 98px}
.up{left:417px;top:1152px;width:38px;height:26px;border-radius:0 0 19px 19px;background:#3a3a3a;display:flex;align-items:center;justify-content:center}
</style>
</head>
<body>
<div class="abs topbar">
  <span><svg width="9" height="9" viewBox="0 0 10 10"><path d="M2 1l2 2-1 1.5c.8 1.4 1.6 2.2 3 3L7.5 6l2 2-1.5 1.8C4.5 9.5.5 5.5.2 2z" fill="#ddd"/></svg>1-800-555-0148</span>
  <span><svg width="10" height="8"><rect x=".5" y=".5" width="9" height="7" fill="none" stroke="#ddd"/><rect x="2" y="2" width="3" height="3" fill="#ddd"/></svg>www.valdocapital.example</span>
  <span><svg width="10" height="8"><rect width="10" height="8" fill="#ddd"/><path d="M0 0l5 4 5-4" stroke="#393939" fill="none"/></svg>info@valdocapital.example</span>
</div>
<div class="abs brand"><span class="brand-mark"></span>Valdo Capital</div>
<nav class="abs nav"><a class="active">Home</a><a>Financial Products</a><a>Teams</a><a>News</a><a>About Us</a><a>Contact Us</a></nav>
<div class="abs rule"></div>

<div class="abs hero" role="img" aria-label="Night skyline of a harbour city with lit towers"></div>
<div class="abs hero-caption"><h1>Valdo Capital</h1><p>Lorem ipsum dolor sit amet, consectetur adipisicing elit, sed do eiusmod tempor incididunt ut labore et dolore magna aliqua...</p><div class="more">Read More ▸</div></div>
<div class="abs arrow" style="left:86px"><svg width="10" height="12"><path d="M8 1L3 6l5 5" stroke="#fff" stroke-width="2.5" fill="none"/></svg></div>
<div class="abs arrow" style="left:741px"><svg width="10" height="12"><path d="M2 1l5 5-5 5" stroke="#fff" stroke-width="2.5" fill="none"/></svg></div>

<div class="abs service" style="left:110px"><h3>INVESTMENT FUNDS</h3><p>Lorem Ipsum is simply dummy text of the printing and typesetting industry. Lorem Ipsum has been the industry's</p></div>
<div class="abs service" style="left:341px"><h3>FINANCE CONSULTANCY</h3><p>Lorem Ipsum is simply dummy text of the printing and typesetting industry. Lorem Ipsum has been the industry's</p></div>
<div class="abs service" style="left:570px"><h3>FINANCE MANAGEMENT</h3><p>Lorem Ipsum is simply dummy text of the printing and typesetting industry. Lorem Ipsum has been the industry's</p></div>
<svg class="abs hex" style="left:91px" viewBox="0 0 40 44"><path d="M20 0l19 11v22L20 44 1 33V11z" fill="var(--hex)"/><rect x="14" y="16" width="12" height="12" rx="2" fill="#fff"/></svg>
<svg class="abs hex" style="left:322px" viewBox="0 0 40 44"><path d="M20 0l19 11v22L20 44 1 33V11z" fill="var(--blue)"/><rect x="12" y="14" width="16" height="12" fill="none" stroke="#fff" stroke-width="2"/><path d="M20 26v6" stroke="#fff" stroke-width="2"/></svg>
<svg class="abs hex" style="left:551px" viewBox="0 0 40 44"><path d="M20 0l19 11v22L20 44 1 33V11z" fill="var(--hex)"/><rect x="12" y="15" width="16" height="11" fill="none" stroke="#fff" stroke-width="2"/><path d="M9 29h22" stroke="#fff" stroke-width="2"/></svg>

<div class="abs section-title" style="left:94px;top:561px">Recent Projects</div>
<div class="abs tile" style="left:94px"><div class="img" role="img" aria-label="Two colleagues reviewing a document at a desk" style="background:linear-gradient(135deg,#cfd6de,#7c8a99)"></div><div class="cap">Lorem Ipsum</div></div>
<div class="abs tile active" style="left:267px"><div class="img" role="img" aria-label="Business meeting around a table, darkened on hover" style="background:linear-gradient(135deg,#5a5f66,#3a3d42);display:flex;align-items:center;justify-content:center"><svg width="16" height="16"><circle cx="6.5" cy="6.5" r="5" stroke="#fff" stroke-width="2" fill="none"/><path d="M10 10l5 5" stroke="#fff" stroke-width="2.5"/></svg></div><div class="cap">Ipsum Dolor</div></div>
<div class="abs tile" style="left:437px"><div class="img" role="img" aria-label="Office team smiling at work" style="background:linear-gradient(135deg,#d9dde2,#8f99a4)"></div><div class="cap">Lorem Ipsum</div></div>
<div class="abs tile" style="left:608px"><div class="img" role="img" aria-label="Group of business people in an office" style="background:linear-gradient(135deg,#9cc3d6,#3a4450)"></div><div class="cap">Ipsum Dolor</div></div>

<div class="abs welcome" style="left:94px;top:762px">
  <h2>Welcome to the <em>VALDO CAPITAL</em></h2>
  <p class="first">Lorem ipsum dolor sit amet, consectetur adipisicing elit, sed do eiusmod tempor incididunt ut labore et dolore magna aliqua. Ut enim ad minim veniam, quis nostrud exercitation ullamco laboris nisi ut aliquip ex ea commodo consequat. Duis aute irure dolor in reprehenderit in voluptate velit esse cillum dolore eu fugiat nulla pariatur. Excepteur sint occaecat cupidatat non proident, sunt in culpa qui officia deserunt mollit anim id est laborum.</p>
  <p class="second">Lorem ipsum dolor sit amet, consectetur adipisicing elit, sed do eiusmod tempor incididunt ut labore et dolore magna aliqua. Ut enim ad minim veniam, quis nostrud exercitation ullamco laboris nisi ut aliquip ex ea commodo consequat. Duis aute irure dolor in reprehenderit in voluptate velit.</p>
</div>
<div class="abs btn" style="left:95px;top:911px;width:59px">Read More</div>

<div class="abs quote" style="left:590px;top:762px"><h2>Request A Quote</h2></div>
<div class="abs field" style="top:798px;height:19px">Enter your name...</div>
<div class="abs field" style="top:825px;height:19px">Enter your email...</div>
<div class="abs field" style="top:851px;height:46px">Enter your comment...</div>
<div class="abs btn" style="left:717px;top:911px;width:50px">Submit</div>

<footer class="abs footer">
  <div class="abs foot-col" style="left:94px;top:28px;width:170px">
    <div style="display:flex;align-items:center;gap:7px;font-size:15px;font-weight:600;color:#eee;margin-bottom:16px"><span style="width:10px;height:10px;background:#eee"></span>Valdo Capital</div>
    <div style="padding-left:14px">Lorem ipsum dolor sit amet consecte-ture adipisicing elit, sed do eiusmod tempor incididunt ut labore et dolore manga eliqua. Ut enim ad minim veniam.</div>
  </div>
  <div class="abs foot-col" style="left:270px;width:150px"><h4>ABOUT US</h4>Lorem ipsum dolor sit amet consecte-ture adipisicing elit, sed do eiusmod tempor incididunt ut labore et dolor manga eliqua. Ut enim ad minim veniam.</div>
  <div class="abs foot-col" style="left:459px;width:140px"><h4>CONTACT US</h4>
    <div style="padding-left:1px">Lorem Ipsum<br>Dolor City&nbsp;&nbsp;&nbsp;123-555-0190<br>Amet&nbsp;&nbsp;&nbsp;&nbsp;&nbsp;&nbsp;&nbsp;&nbsp;&nbsp;123-555-0190</div>
    <div style="margin-top:4px;line-height:17px">☏&nbsp; 1-800-555-0148<br>▣&nbsp; www.valdocapital.example<br>✉&nbsp; info@valdocapital.example</div>
  </div>
  <div class="abs foot-col" style="left:605px;width:165px"><h4>GET IN TOUCH</h4>
    <div style="font-size:7.8px;line-height:14px">If you ahve any questions you can conatct us via our contact form <span style="color:var(--blue)">here</span>, or follow us on social networks.</div>
    <div class="social"><i></i><i></i><i></i><i class="on"></i><i></i></div>
  </div>
</footer>
<div class="abs bottom"><span>Copyright© 2014 Valdo Capital. All Rights Reserved</span><span>Terms &amp; Condition&nbsp;&nbsp;&nbsp;&nbsp;&nbsp;|&nbsp;&nbsp;&nbsp;&nbsp;&nbsp;Privacy Policy</span></div>
<div class="abs up"><svg width="10" height="7"><path d="M5 0l5 7H0z" fill="#999"/></svg></div>
</body>
</html>
```